Re-Design my old Business Card

We need a new business card design. The current layout is lacking good design.
We manufacture building products and also offers services (www.tqconstructlabs.com.au)
I've attached the old business card to show you what we don't want.
I've also attached the new logo in two styles for you to chose from.
The final design should communicate smarter building design and lifestyle, with a clean and crisp designed card.

Target Market(s)

Architects, building companies

Industry/Entity Type

Business

Contact Information for Business Card

See attached old business cards for all details to include

Font styles to use
Sans Serif

Colors
9bcb3b

Requirements
Must have
• Clean crisp look
Nice to have
• Totally up to you

```html
<!DOCTYPE html>
<html lang="en">
<head>
<meta charset="utf-8">
<title>TQ Construct Labs – Business Card</title>
<link href="https://fonts.googleapis.com/css2?family=Lato:wght@400;700;900&display=swap" rel="stylesheet">
<style>
  :root {
    --green: #9bcb3b;
    --stage: #1c1c1c;
    --card-white: #fbfbfb;
    --ink: #3a3a3a;
    --ink-soft: #555555;
    --card-dark: #4a4a4a;
    --card-dark-text: #b9b9b9;
    --band: #c4c4c4;
    --band-text: #2f2f2f;
  }
  * { margin: 0; padding: 0; box-sizing: border-box; }
  html, body { width: 1200px; height: 873px; overflow: hidden; }
  body {
    background: var(--stage);
    font-family: "Lato", Arial, sans-serif;
    position: relative;
  }
  .card {
    position: absolute;
    top: 280px;
    width: 530px;
    height: 310px;
    border-radius: 14px;
    overflow: hidden;
  }
  /* Front */
  .card--front { left: 45px; background: var(--card-white); }
  .brand {
    position: absolute; left: 34px; top: 40px;
    display: flex; align-items: center; gap: 10px;
  }
  .brand__square { width: 26px; height: 26px; background: var(--green); }
  .brand__name {
    font-size: 25px; font-weight: 700; color: var(--green);
    letter-spacing: 0.5px; text-transform: uppercase;
  }
  .person {
    position: absolute; right: 34px; top: 110px; text-align: right;
  }
  .person__name { font-size: 19px; font-weight: 700; color: var(--green); }
  .person__role { font-size: 12px; color: var(--ink-soft); margin-top: 3px; }
  .office { position: absolute; right: 34px; top: 168px; text-align: right; }
  .office__label { font-size: 12px; color: var(--ink-soft); text-decoration: underline; }
  .office__address { font-size: 14px; font-weight: 700; color: var(--green); line-height: 1.35; margin-top: 3px; }
  .contacts {
    position: absolute; left: 34px; bottom: 28px; list-style: none;
  }
  .contacts li {
    display: flex; align-items: center; gap: 12px;
    font-size: 15px; color: var(--ink); letter-spacing: 0.5px; height: 24px;
  }
  .contacts svg { width: 15px; height: 15px; fill: var(--green); flex: none; }
  /* Back */
  .card--back { left: 625px; background: var(--card-dark); }
  .back-brand {
    position: absolute; left: 0; right: 0; top: 70px;
    display: flex; justify-content: center; align-items: center; gap: 12px;
  }
  .back-brand__square { width: 34px; height: 34px; background: var(--card-dark-text); }
  .back-brand__name {
    font-size: 32px; font-weight: 700; color: var(--card-dark-text);
    letter-spacing: 1px; text-transform: uppercase;
  }
  .services {
    position: absolute; left: 0; right: 0; top: 150px; text-align: center;
    font-size: 17px; font-weight: 700; color: var(--card-dark-text); line-height: 1.45;
  }
  .services__dot { margin: 0 8px; }
  .url-band {
    position: absolute; left: 0; right: 0; bottom: 0; height: 46px;
    background: var(--band);
    display: flex; align-items: center; justify-content: center;
    font-size: 16px; font-weight: 900; color: var(--band-text); letter-spacing: 1.5px;
  }
</style>
</head>
<body>
  <section class="card card--front">
    <div class="brand">
      <span class="brand__square"></span>
      <span class="brand__name">TQ Construct Labs</span>
    </div>
    <div class="person">
      <p class="person__name">Marcus Hale</p>
      <p class="person__role">Account Manager Qld / Northern NSW</p>
    </div>
    <div class="office">
      <p class="office__label">Head Office:</p>
      <p class="office__address">Unit 4/27 Larkin Street<br>Riverton QLD 4170</p>
    </div>
    <ul class="contacts">
      <li>
        <svg viewBox="0 0 16 16" aria-hidden="true"><path d="M3 1h3l1.5 4-2 1.3a9 9 0 0 0 4.2 4.2L11 8.5 15 10v3a2 2 0 0 1-2 2A12 12 0 0 1 1 3a2 2 0 0 1 2-2z"/></svg>
        1300 555 210
      </li>
      <li>
        <svg viewBox="0 0 16 16" aria-hidden="true"><path d="M4 0h8a1 1 0 0 1 1 1v14a1 1 0 0 1-1 1H4a1 1 0 0 1-1-1V1a1 1 0 0 1 1-1zm1 2v10h6V2zm3 11a1 1 0 1 0 0 2 1 1 0 0 0 0-2z"/></svg>
        0400 555 372
      </li>
      <li>
        <svg viewBox="0 0 16 16" aria-hidden="true"><path d="M4 1h8v4H4zM1 6h14v6h-3v3H4v-3H1zm4 4v4h6v-4z"/></svg>
        1300 555 211
      </li>
      <li>
        <svg viewBox="0 0 16 16" aria-hidden="true"><path d="M1 3h14v10H1zm1.5 1.2L8 8.5l5.5-4.3z"/></svg>
        marcus@tqconstructlabs.com.au
      </li>
    </ul>
  </section>

  <section class="card card--back">
    <div class="back-brand">
      <span class="back-brand__square"></span>
      <span class="back-brand__name">TQ Construct Labs</span>
    </div>
    <p class="services">
      Energy Efficency Consulting<span class="services__dot">•</span>Insulation Manufacturer<br>
      Building Science Technologies
    </p>
    <div class="url-band">www.tqconstructlabs.com.au</div>
  </section>
</body>
</html>
```